"Velmora Crest" sexual performance enhancement pill bottle label needed.

This should be interesting...

I am starting a line of sexual performance enhancement products. This will be the first of several products basically. Keep in mind, I am the type of business person to stay with one company for years if they provide me with quality work.

This particular product is a male sexual performance pill. The name of the product is "Velmora Crest." The packaging of the pills are a black bottle with a white top. Label on the product example would be perfect but at a minimum I have attached a "template" for your guidance.

Some of the technical aspects of this are as follows:

-File Format: Illustrator CS6 is preferred. (Winner must provide artwork in layer and can not flatten artwork.)
-Resolution: 300 dpi minimum
-Bleed: 1/16th (0.0625") inch from edge of label
-Color Mode: CMYK only or must be converted to CMYK for final production

Lastly, this is your project as a designer, artist, creator, this is essentially a piece of you that will be sold and known by thousands of people. I have no color scheme that I prefer, just use the template and follow the layout. If you have any further questions, please feel free to contact me at any time.
Updates

Quick note on the product and what it does: -Powerful, long lasting, harder erections -Works in a minutes and last for hours -Enhances sexual desire and drive Thank you for your ideas...

Project Deadline Extended
Reason: We decided to extent the project for a few more days to let the last few concepts come in. So far things are looking really good and we definitely have seen some amazing designs. Thank you for your hard work and amazing creativity. Looking forward to seeing what we have come in the next couple of day. Very respectfully, Brev

ONLY THREE DAYS LEFT!!!! Please submit your ideas as soon as possible. And as always, thank you for your help!!! V/r, Brev

Industry/Entity Type

Graphic Design

```html
<!DOCTYPE html>
<html lang="en">
<head>
<meta charset="utf-8">
<title>Velmora Crest – Horny Goat Weed 1600 Label</title>
<link href="https://fonts.googleapis.com/css2?family=Raleway:wght@200;400&family=Cormorant+Garamond:wght@500&family=Montserrat:wght@400;600&display=swap" rel="stylesheet">
<style>
  :root {
    --backdrop-light: #f2f2f2;
    --backdrop-dark: #cfcfcf;
    --label-black: #101010;
    --label-edge: #1c1c1c;
    --ink-white: #f4f4f4;
    --ink-soft: #c9c9c9;
    --ink-muted: #a8a8a8;
    --figure-light: #8a8a8a;
    --figure-dark: #2a2a2a;
  }
  * { margin: 0; padding: 0; box-sizing: border-box; }
  html, body { width: 1200px; height: 900px; overflow: hidden; }
  body {
    background: radial-gradient(ellipse at 50% 40%, var(--backdrop-light) 0%, var(--backdrop-dark) 100%);
    display: flex;
    align-items: center;
    justify-content: center;
  }
  .label {
    width: 1140px;
    height: 440px;
    background: var(--label-black);
    border: 1px solid var(--label-edge);
    display: flex;
  }
  .panel { height: 100%; }

  /* Left side: directions and warnings */
  .panel--info {
    width: 340px;
    padding: 40px 34px 0 40px;
    font-family: "Montserrat", sans-serif;
    font-size: 11px;
    line-height: 1.55;
    color: var(--ink-soft);
  }
  .info__block { margin-bottom: 14px; }
  .info__heading { font-weight: 600; color: var(--ink-white); }
  .info__notice {
    margin-top: 60px;
    border: 1px solid var(--ink-soft);
    border-radius: 8px;
    padding: 8px 12px;
    font-size: 10px;
    line-height: 1.4;
  }

  /* Front panel */
  .panel--front {
    width: 460px;
    display: flex;
    flex-direction: column;
    align-items: center;
    padding-top: 26px;
  }
  .label__figure {
    width: 96px;
    height: 230px;
    border-radius: 48% 48% 30% 30%;
    background: linear-gradient(180deg, var(--figure-light) 0%, var(--figure-dark) 100%);
    opacity: 0.75;
  }
  .label__brand {
    font-family: "Raleway", sans-serif;
    font-weight: 200;
    font-size: 40px;
    letter-spacing: 0.5px;
    color: var(--ink-white);
    margin-top: 8px;
    line-height: 1;
    white-space: nowrap;
  }
  .label__product {
    font-family: "Cormorant Garamond", serif;
    font-weight: 500;
    font-size: 25px;
    color: var(--ink-white);
    margin-top: 10px;
    line-height: 1;
  }
  .label__category {
    font-family: "Montserrat", sans-serif;
    font-weight: 600;
    font-size: 15px;
    letter-spacing: 1.5px;
    color: var(--ink-white);
    margin-top: 22px;
  }
  .label__claims {
    font-family: "Montserrat", sans-serif;
    font-size: 12px;
    letter-spacing: 0.5px;
    color: var(--ink-soft);
    margin-top: 3px;
  }
  .label__count {
    font-family: "Montserrat", sans-serif;
    font-weight: 600;
    font-size: 9px;
    letter-spacing: 1.5px;
    color: var(--ink-muted);
    margin-top: 22px;
  }

  /* Right side: facts frame */
  .panel--facts {
    width: 340px;
    padding: 40px 40px 0 10px;
    font-family: "Montserrat", sans-serif;
    color: var(--ink-white);
  }
  .facts__frame {
    width: 100%;
    height: 250px;
    border: 3px solid var(--ink-white);
    padding: 8px 12px;
  }
  .facts__title { font-weight: 600; font-size: 18px; }
  .facts__maker {
    margin-top: 14px;
    font-size: 11px;
    color: var(--ink-soft);
  }
</style>
</head>
<body>
  <section class="label">
    <div class="panel panel--info">
      <p class="info__block"><span class="info__heading">Directions:</span> Take 2 capsules daily with water, or as directed, about 1 hour before activity.</p>
      <p class="info__block"><span class="info__heading">Warning:</span> Do not exceed the recommended dose. Not intended for use by persons under the age of 18. Do not use if pregnant or nursing. Consult your doctor before use if you have any medical conditions, or take prescription drugs.</p>
      <p class="info__notice">Keep out of reach of children. Store in a cool, dry place.</p>
    </div>

    <div class="panel panel--front">
      <div class="label__figure" role="img" aria-label="Line illustration of a female figure with raised arms and flowing hair"></div>
      <h1 class="label__brand">VELMORA CREST</h1>
      <p class="label__product">HORNY GOAT WEED 1600</p>
      <p class="label__category">DIETARY SUPPLEMENT</p>
      <p class="label__claims">Max Strength | Pure and Potent</p>
      <p class="label__count">60 CAPSULES</p>
    </div>

    <div class="panel panel--facts">
      <div class="facts__frame">
        <p class="facts__title">Supplement Facts</p>
      </div>
      <p class="facts__maker">Manufactured for Velmora Crest</p>
    </div>
  </section>
</body>
</html>
```